QHX Compliant Dietary Supplement Label for Nutritional Company

We are in need of a label for our line of 20+ dietary supplements that are specifically formulated to balance body chemistry and match the biochemical individuality of our users based on hair tissue mineral analysis.

We have a line of approximately 20 different dietary supplements that will require use of new label in both a small (90 capsule) and large (180 capsule) size. We will start with the initial label in which Product name, Supplement Facts, and Ingredient list will need to be modified for each particular product thereafter.

The label will be placed on a transparent blue bottle with the color of lid being decided after label design. We are open to a transparent light amber bottle with black lid but blue is our preference.

We would like the majority of the label to be blue. Solid blue, fading of blue to darker blue/black, or subtle background designs are welcome with involvement of white and hints of orange. We do not want pictorial images on the label.

Label size:
Small bottle (120cc): Label size ~ 2.25” x 5.875”
Large bottle (200cc): Label size ~ 2.75” x 7.625”

Front:
-Logo near top of label with product name and description in middle and capsule count near the bottom

Right Side:
-Supplement Facts: See current product image below in brief
-Ingredient list: See current product image below in brief
-Manufactured for: See image below (This is on the left side of our current bottle and would like it moved to the bottom of the right side)

Left side:
-Suggested use: See current product image below in brief
-Leave room for possible warning statement
-Leave room for possible lot number printing
-Keep out of the reach of children.

The first files below are our current supplement label with product information. This information is what is needed on the label and will likely need some adjustments as we are updating our line of supplements and changes in QHX requirements.

The following files are the logo files and color palette.

The remaining files are some designs we came across for inspiration.

Thank you.

Target Market(s)

Health Care Profressionals

Industry/Entity Type

Health Care and Nutrition

Requirements
Nice to have
• Product name needs to be on same line in all one color
Should not have
• Pictorial Images

```html
<!DOCTYPE html>
<html lang="en">
<head>
<meta charset="utf-8">
<title>CORTA-BAL Adrenal Supplement Label</title>
<link href="https://fonts.googleapis.com/css2?family=Montserrat:wght@400;600;700&display=swap" rel="stylesheet">
<style>
  :root {
    --page-bg: #f4f4f4;
    --navy-deep: #222b52;
    --navy-mid: #2f3f73;
    --slate: #4a557c;
    --edge-light: #7d89ad;
    --white: #f7f7f9;
    --orange: #ee7a35;
    --orange-light: #f59a5e;
    --label-ink: #2e3566;
  }
  html, body {
    margin: 0;
    padding: 0;
    width: 1200px;
    height: 960px;
    overflow: hidden;
    background: var(--page-bg);
    font-family: "Montserrat", sans-serif;
  }
  .canvas {
    position: relative;
    width: 1200px;
    height: 960px;
  }
  .label {
    position: absolute;
    left: 248px;
    top: 42px;
    width: 705px;
    height: 878px;
    overflow: hidden;
    background:
      linear-gradient(180deg, rgba(0,0,0,0) 55%, rgba(120,140,190,0.22) 100%),
      linear-gradient(90deg,
        var(--edge-light) 0%,
        var(--navy-deep) 21%,
        #3d4366 33%,
        var(--slate) 52%,
        var(--navy-deep) 67%,
        #3e4770 80%,
        #5f6a8e 100%);
  }
  .brand {
    position: absolute;
    left: 300px;
    top: 165px;
    width: 360px;
    display: flex;
    align-items: center;
    gap: 14px;
    color: var(--white);
  }
  .brand-dot {
    width: 34px;
    height: 34px;
    border: 4px solid var(--orange);
    border-radius: 50%;
    box-sizing: border-box;
    flex: none;
  }
  .brand-name {
    font-weight: 400;
    font-size: 40px;
    letter-spacing: 2px;
    line-height: 1.1;
  }
  .brand-name span {
    display: block;
    font-size: 17px;
    letter-spacing: 6px;
  }
  .product-name {
    position: absolute;
    left: 46px;
    margin: 0;
    font-weight: 400;
    font-size: 150px;
    line-height: 1;
    color: var(--white);
    letter-spacing: 1px;
  }
  .product-name.top { top: 318px; }
  .product-name.bottom { top: 478px; }
  .name-dash {
    position: absolute;
    left: 248px;
    top: 468px;
    width: 40px;
    height: 12px;
    background: var(--orange);
  }
  .description {
    position: absolute;
    left: 53px;
    right: 0;
    top: 635px;
    height: 34px;
    background: linear-gradient(90deg, var(--orange) 60%, var(--orange-light) 100%);
    color: var(--label-ink);
    font-weight: 700;
    font-size: 31px;
    line-height: 34px;
    padding-left: 8px;
    letter-spacing: 0.5px;
  }
  .count {
    position: absolute;
    left: 62px;
    top: 760px;
    display: flex;
    align-items: center;
    gap: 30px;
  }
  .count-number {
    font-size: 78px;
    font-weight: 400;
    color: var(--white);
    line-height: 1;
  }
  .count-unit {
    background: var(--orange);
    color: var(--label-ink);
    font-weight: 700;
    font-size: 29px;
    line-height: 31px;
    padding: 0 10px;
    letter-spacing: 0.5px;
  }
</style>
</head>
<body>
<div class="canvas">
  <section class="label">
    <div class="brand">
      <div class="brand-dot"></div>
      <div class="brand-name">KELVARA<span>LABORATORIES</span></div>
    </div>
    <h1 class="product-name top">CORTA</h1>
    <div class="name-dash"></div>
    <h1 class="product-name bottom">BAL</h1>
    <div class="description">ADRENAL SUPPLEMENT</div>
    <div class="count">
      <span class="count-number">90</span>
      <span class="count-unit">CAPSULES</span>
    </div>
  </section>
</div>
</body>
</html>
```